Building company buisness cards

We are looking for a sharp modern new look for our business cards.
We are a New Zealand based company that specialises in house and land packages.
We have attached a photo of the current logo and would like to see if it can be improved somehow if needed.
We are open to any colours but we have chosen green at this stage.
Feel free to change the font and make the logo smarter looking.
Play with the colours and see what looks best.

We want a card that looks so good know one will want to throw it away!

Target Market(s)

Home buyers

Industry/Entity Type

Building

Contact Information for Business Card

Derek Tolvane
0217394062
dtolvane@quillmarkhomesteads.co.nz
quillmarkhomesteads.co.nz

Font styles to use
Serif
Sans Serif

Colors

Designer to choose colors to be used in the design.

Requirements
Must have
• Logo and company name on one side, details on the other side
Nice to have
• Color codes for the original green are HEX #4a8028, RGB(74,128,40), CMYK(42,0,69,50)
• Round corners, Raised and/or spot UV

```html
<!DOCTYPE html>
<html lang="en">
<head>
<meta charset="utf-8">
<title>Quillmark Homesteads – Business Card</title>
<link rel="stylesheet" href="https://fonts.googleapis.com/css2?family=Montserrat:wght@400;500;700;800&display=swap">
<style>
  :root {
    --brand-green: #4a7a3e;
    --brand-green-dark: #3f6b34;
    --brand-green-light: #5e8f4f;
    --paper: #ffffff;
    --paper-shade: #f1f1f1;
    --band-grey: #a9a7a9;
    --emblem-grey: #e4e7e2;
    --ink: #222222;
    --stage: #ecebe8;
  }
  html, body {
    margin: 0;
    padding: 0;
    width: 1200px;
    height: 1021px;
    overflow: hidden;
    background: var(--stage);
    font-family: "Montserrat", Arial, sans-serif;
  }
  .canvas {
    position: relative;
    width: 1200px;
    height: 1021px;
  }
  .card {
    position: absolute;
    left: 280px;
    width: 640px;
    height: 390px;
    border-radius: 24px;
    overflow: hidden;
    box-shadow: 0 10px 28px rgba(0,0,0,0.18);
  }

  /* Back side */
  .card-back {
    top: 80px;
    background: var(--brand-green);
  }
  .back-pattern {
    position: absolute;
    inset: 0;
    background: linear-gradient(120deg, var(--brand-green-light) 0%, var(--brand-green) 55%, var(--brand-green-dark) 100%);
  }
  .back-wordmark {
    position: absolute;
    right: 52px;
    bottom: 58px;
    color: var(--paper);
    font-weight: 800;
    line-height: 0.95;
    display: flex;
    align-items: center;
    gap: 14px;
  }
  .back-wordmark .mark-square {
    width: 34px;
    height: 34px;
    background: var(--paper);
  }
  .back-wordmark .name-top { font-size: 42px; letter-spacing: 0.5px; display: block; }
  .back-wordmark .name-bottom { font-size: 24px; display: block; padding-left: 2px; }

  /* Front side */
  .card-front {
    top: 530px;
    background: linear-gradient(160deg, var(--paper) 0%, var(--paper-shade) 100%);
  }
  .front-emblem {
    position: absolute;
    right: 20px;
    top: 100px;
    width: 300px;
    height: 270px;
    border-radius: 30px;
    background: radial-gradient(ellipse at 50% 45%, var(--emblem-grey) 0%, rgba(228,231,226,0) 72%);
  }
  .front-swoosh {
    position: absolute;
    inset: 0;
  }
  .front-wordmark {
    position: absolute;
    left: 46px;
    top: 48px;
    color: var(--brand-green);
    font-weight: 800;
    line-height: 0.95;
  }
  .front-wordmark .name-top { font-size: 46px; display: block; }
  .front-wordmark .name-bottom { font-size: 26px; display: block; padding-left: 2px; }
  .holder {
    position: absolute;
    right: 70px;
    top: 172px;
    text-align: right;
  }
  .holder-name {
    margin: 0;
    color: var(--brand-green);
    font-weight: 700;
    font-size: 25px;
  }
  .holder-role {
    margin: 2px 0 0;
    color: var(--ink);
    font-weight: 500;
    font-size: 17px;
  }
  .contact-list {
    position: absolute;
    left: 46px;
    top: 262px;
    margin: 0;
    padding: 0;
    list-style: none;
    color: var(--ink);
    font-size: 17px;
    line-height: 25px;
  }
  .contact-list li {
    display: flex;
    align-items: center;
    gap: 9px;
  }
  .contact-list svg {
    width: 15px;
    height: 15px;
    flex: none;
  }
</style>
</head>
<body>
<main class="canvas">

  <section class="card card-back" aria-label="Card back">
    <div class="back-pattern" role="img" aria-label="Embossed repeating house emblem pattern on green"></div>
    <div class="back-wordmark">
      <span class="mark-square"></span>
      <span>
        <span class="name-top">quillmark</span>
        <span class="name-bottom">homesteads.</span>
      </span>
    </div>
  </section>

  <section class="card card-front" aria-label="Card front">
    <div class="front-emblem" role="img" aria-label="Faint large house emblem watermark"></div>
    <svg class="front-swoosh" viewBox="0 0 640 390" preserveAspectRatio="none" aria-hidden="true">
      <path d="M250 390 C400 330 540 300 640 210 L640 390 Z" fill="var(--band-grey)"/>
      <path d="M280 390 C420 340 550 320 640 240 L640 390 Z" fill="var(--brand-green)"/>
    </svg>

    <div class="front-wordmark">
      <span class="name-top">quillmark</span>
      <span class="name-bottom">homesteads.</span>
    </div>

    <div class="holder">
      <p class="holder-name">Derek Tolvane</p>
      <p class="holder-role">Founder</p>
    </div>

    <ul class="contact-list">
      <li>
        <svg viewBox="0 0 16 16" aria-hidden="true"><path d="M3.5 1.5l2.5 0 1 3.5-1.6 1.2a8 8 0 0 0 4.4 4.4L11 9l3.5 1v2.5c0 1-1 2-2 2C6.5 14.5 1.5 9.5 1.5 3.5c0-1 1-2 2-2z" fill="var(--brand-green)"/></svg>
        <span>0217394062</span>
      </li>
      <li>
        <svg viewBox="0 0 16 16" aria-hidden="true"><rect x="1.5" y="3.5" width="13" height="9" fill="none" stroke="var(--brand-green)" stroke-width="1.6"/><path d="M1.5 3.5L8 9l6.5-5.5" fill="none" stroke="var(--brand-green)" stroke-width="1.6"/></svg>
        <span>dtolvane@quillmarkhomesteads.co.nz</span>
      </li>
      <li>
        <svg viewBox="0 0 16 16" aria-hidden="true"><circle cx="8" cy="8" r="6.5" fill="none" stroke="var(--brand-green)" stroke-width="1.5"/><ellipse cx="8" cy="8" rx="2.8" ry="6.5" fill="none" stroke="var(--brand-green)" stroke-width="1.2"/><path d="M1.5 8h13" stroke="var(--brand-green)" stroke-width="1.2"/></svg>
        <span>quillmarkhomesteads.co.nz</span>
      </li>
    </ul>
  </section>

</main>
</body>
</html>
```